Life Coaching Business Needs A Business card Design

Earthy, quirky, colourful business card needed for a Life Coaching company supporting same sex attracted young men. My coaching supports these same sex attracted guys to find their own inner happiness and passion and purpose and not feel they need to live a 'label' or follow the crowd. It its about personal passion and happiness.
IT IS ABOUT THEIR INNER RAINBOW.
Some aspects of rainbow would be important to the design.

I have uploaded a recently designed POSTCARD and the business card will be a smaller version with much less information. The Business Card will take the very important parts of the POSTCARD

Front of Card.......
I'm thinking the front of the card would need to be the large LOGO with a rainbow emerging from the inside...from the heart...the core. This will almost FILL the front of the card. This has been uploaded for you. IMMEDIATELY under the LOGO ( to make it a part of the logo) would be the words COACHING * WELLNESS *
The statement HAPPINESS and WHOLENESS for MEN WHO DATE MEN should feature across the front of the BUSINESS CARD as it does across the back of the POSTCARD. It will need some kind of rainbow background to the statement as it does on the POSTCARD. Needs to be a different rainbow pattern. See what you think.

That could be the front. On a black background.
I wonder what you think and what you will do with that.

Back Of Card.

I'm hoping the back of the BUSINESS card could be the PHOTO section from the back of the POSTCARD. The photo and the quote. I will make the quote shorter to fit better on a BUSINESS card. It can be written in a handwriting style to make it look like a personal message from me as it is on the POSTCARD.

All across the top of the back of the card could be the statement
MOTIVATION and INSPIRATION for MEN WHO DATE MEN

Across the card under the statement would be the three contacts
www.brightvolume.com *0437 615 203*tom@brightvolume.com

It would be great to see if you have a different idea for this arrangement.

At the bottom of the Business card ( as on the photo at on the POSTCARD ) would be my name with a description underneath

Tom Walbrook
Transformational Life Coach * Happiness Guru * Change catalyst

What do you think ? Will all of this work ?
I hope I haven't been too prescriptive. I don't want this to be a boring job for you.

Looking forward to hearing what you think and seeing what you come up with.

Target Market(s)

Same sex attracted males. All ages. Especially those who are struggling or unhappy or depressed. The card must be uplifting and it must SPEAK to these guys. I want ti include a personal 'quote' from me ( in handwriting font as if I wrote to them ) to encourage these guys to get the help they need.

Industry/Entity Type

Business

Contact Information for Business Card

I have been quite prescriptive but am happy to see what the designer might come up with as well. I don't mean to make it boring for the designer. I have included names and contact details in the brief. Please let me know if I need to give you more details.

Requirements
Must have
• LOGO
• A clear statement on the front and back to state clearly who the coaching service is for. I have explained these in the brief.
• Pic of me to fill the back of the card with room to write the details on. I have other pics if needed.
• Needs to be casual and inviting. Almost informal and organic. Quite earthy to balance with the 'lifestyle' these guys can often live.
Nice to have
• Colour and ideas to keep it uncluttered.
Should not have
• Formal design or 'business' like feel.

```html
<!DOCTYPE html>
<html lang="en">
<head>
<meta charset="utf-8">
<title>Tom Walbrook – Business Card</title>
<link href="https://fonts.googleapis.com/css2?family=Lato:wght@400;700;900&display=swap" rel="stylesheet">
<style>
  :root {
    --page-bg: #3a3b3d;
    --card-bg: #0b0b0c;
    --text-light: #ffffff;
    --quote-ink: #3a3a3a;
    --r-blue: #0000ff;
    --r-sky: #0a7fc9;
    --r-magenta: #ff00ff;
    --r-green: #00ff00;
    --r-yellow: #ffff00;
    --r-orange: #e8631a;
    --r-red: #df2222;
    --sky-top: #e9efee;
    --sky-mid: #f6f8f4;
    --grass-light: #7fae3e;
    --grass-dark: #3f6b1c;
  }
  * { margin: 0; padding: 0; box-sizing: border-box; }
  html, body { width: 1200px; height: 900px; overflow: hidden; }
  body {
    background: var(--page-bg);
    font-family: "Lato", sans-serif;
    position: relative;
  }
  .card {
    position: absolute;
    left: 70px; top: 122px;
    width: 1063px; height: 636px;
    background: var(--card-bg);
    border-radius: 30px;
  }
  .headline {
    position: absolute;
    left: 55px; top: 28px;
    width: 950px;
    font-size: 34.5px;
    font-weight: 900;
    letter-spacing: 0.3px;
    white-space: nowrap;
  }
  .headline span { display: inline-block; }
  .hl-motivation { background: linear-gradient(90deg, #1a7fd0, #7d62c8); -webkit-background-clip: text; background-clip: text; color: transparent; }
  .hl-and { color: #2a7ac8; font-size: 30px; }
  .hl-inspiration { background: linear-gradient(90deg, #0c8fc8, #1aa36a, #7dc21e); -webkit-background-clip: text; background-clip: text; color: transparent; }
  .hl-for { color: #f2c400; font-size: 30px; }
  .hl-men { color: #ffd500; }
  .hl-who { color: #f6a000; }
  .hl-date { color: #ea5a1c; }
  .hl-men-end { color: #df2a22; }

  .rainbow-strip {
    position: absolute;
    top: 78px;
    width: 43px;
    display: flex; flex-direction: column;
  }
  .rainbow-strip.left { left: 0; }
  .rainbow-strip.right { right: 0; }
  .rainbow-strip i { display: block; height: 50px; }
  .rainbow-strip i:nth-child(1) { background: var(--r-blue); }
  .rainbow-strip i:nth-child(2) { background: var(--r-sky); }
  .rainbow-strip i:nth-child(3) { background: var(--r-magenta); }
  .rainbow-strip i:nth-child(4) { background: var(--r-green); }
  .rainbow-strip i:nth-child(5) { background: var(--r-yellow); }
  .rainbow-strip i:nth-child(6) { background: var(--r-orange); }
  .rainbow-strip i:nth-child(7) { background: var(--r-red); }

  .photo-panel {
    position: absolute;
    left: 242px; top: 86px;
    width: 614px; height: 355px;
    background: linear-gradient(180deg, var(--sky-top) 0%, var(--sky-mid) 55%, #e6ecdc 76%, var(--grass-light) 80%, var(--grass-dark) 100%);
  }
  .photo-panel .coach-figure {
    position: absolute;
    left: 482px; top: 34px;
    width: 108px; height: 316px;
    background: linear-gradient(180deg, rgba(90,80,70,0.22), rgba(60,50,40,0.32));
    border-radius: 50px 50px 10px 10px;
  }
  .quote {
    position: absolute;
    left: 260px; top: 114px;
    font-size: 21.5px;
    line-height: 32.5px;
    color: var(--quote-ink);
    white-space: nowrap;
  }
  .quote span { display: block; }

  .coach-name {
    position: absolute;
    left: 52px; top: 447px;
    font-size: 37px;
    font-weight: 900;
    letter-spacing: 0.5px;
    background: linear-gradient(90deg, #1f7fc8 0%, #3aa060 22%, #f0d000 45%, #f29a00 65%, #e03a22 100%);
    -webkit-background-clip: text; background-clip: text; color: transparent;
    white-space: nowrap;
  }
  .coach-roles {
    position: absolute;
    left: 55px; top: 495px;
    list-style: none;
    color: var(--text-light);
    font-size: 22px;
    line-height: 33px;
  }
  .contact-list {
    position: absolute;
    right: 91px; top: 489px;
    list-style: none;
    text-align: right;
    color: var(--text-light);
    font-size: 22.5px;
    line-height: 35.5px;
  }
</style>
</head>
<body>
  <section class="card">
    <h1 class="headline">
      <span class="hl-motivation">MOTIVATION</span>
      <span class="hl-and">and</span>
      <span class="hl-inspiration">INSPIRATION</span>
      <span class="hl-for">for</span>
      <span class="hl-men">MEN</span><span class="hl-who">&nbsp;WHO</span>
      <span class="hl-date">DATE</span>
      <span class="hl-men-end">MEN</span>
    </h1>

    <div class="rainbow-strip left"><i></i><i></i><i></i><i></i><i></i><i></i><i></i></div>
    <div class="rainbow-strip right"><i></i><i></i><i></i><i></i><i></i><i></i><i></i></div>

    <div class="photo-panel" role="img" aria-label="Photo of the coach standing barefoot on a grassy field under a bright sky">
      <div class="coach-figure"></div>
    </div>
    <p class="quote">
      <span>“My Coaching is about helping you change</span>
      <span>whatever is making you unhappy or confused.</span>
      <span>It is about building an inspiring, INTEGRATED</span>
      <span>life story for Men Who Date Men. You can</span>
      <span>create a passionate life that celebrates your</span>
      <span>unique rainbow GREATNESS...day after</span>
      <span>amazing day. I can help..”</span>
    </p>

    <h2 class="coach-name">TOM WALBROOK</h2>
    <ul class="coach-roles">
      <li>Transformational Life Coach</li>
      <li>Happiness Guru</li>
      <li>Change catalyst</li>
    </ul>

    <ul class="contact-list">
      <li>www.brightvolume.com</li>
      <li>0437 615 203</li>
      <li>tom@brightvolume.com</li>
    </ul>
  </section>
</body>
</html>
```